Harborline Renewal Business Card Design

Professional and clean design. The design colors should flow with the logo. Two-sided card with the website on the back which is:

www.HarborlineRenewal.example.

"Specializing in Water Damage Restoration"

On the front I need the name, email, phone, and logo.

Name: Darnell Quisby
Email: Darnell@HarborlineRenewal.example
Phone: 555-318-2046 for now

I only have the Preview and Thumbnail right now but should have the source files uploaded within a day or two.

Target Market(s)

Flood victims, home owners with water damage from busted pipes etc...

Industry/Entity Type

Business

Contact Information for Business Card

Name: Darnell Quisby

Font styles to use
Serif
Sans Serif

Requirements
Must have
• Business Card Details Info

```html
<!DOCTYPE html>
<html lang="en">
<head>
<meta charset="UTF-8">
<title>Harborline Renewal — Business Cards</title>
<link href="https://fonts.googleapis.com/css2?family=Cinzel:wght@400;600&family=Open+Sans:wght@400;600&display=swap" rel="stylesheet">
<style>
  :root {
    --page-bg: #e9e6e2;
    --card-dark: #1d1d1f;
    --card-dark-2: #262628;
    --brand-blue: #2a8fd6;
    --panel-blue: #3a9ee0;
    --crescent-blue: #5cbcf0;
    --ink-light: #ffffff;
    --ink-tagline: #2f8fd0;
  }
  * { box-sizing: border-box; margin: 0; padding: 0; }
  html, body { width: 1200px; height: 1120px; overflow: hidden; }
  body {
    background: var(--page-bg);
    position: relative;
    font-family: "Open Sans", Arial, sans-serif;
  }
  .card {
    position: absolute;
    left: 160px;
    width: 880px;
    height: 503px;
    background: radial-gradient(circle at 40% 40%, var(--card-dark-2), var(--card-dark));
    overflow: hidden;
    box-shadow: 0 8px 24px rgba(0,0,0,0.25);
  }
  .card--back { top: 38px; }
  .card--front { top: 579px; }

  .brand {
    position: absolute;
    display: flex;
    flex-direction: column;
    align-items: center;
    text-align: center;
  }
  .brand__mark {
    border-radius: 50%;
    background: var(--brand-blue);
  }
  .brand__name {
    font-family: "Cinzel", "Times New Roman", serif;
    font-weight: 600;
    color: var(--brand-blue);
    letter-spacing: 0.04em;
    line-height: 1.1;
  }

  .card--back .brand { left: 0; right: 0; top: 92px; }
  .card--back .brand__mark { width: 108px; height: 108px; margin-bottom: 26px; }
  .card--back .brand__name { font-size: 54px; }
  .tagline {
    margin-top: 34px;
    font-family: "Cinzel", "Times New Roman", serif;
    font-size: 19px;
    letter-spacing: 0.06em;
    color: var(--ink-tagline);
  }

  .card--front .brand { left: 40px; width: 380px; top: 110px; }
  .card--front .brand__mark { width: 96px; height: 96px; margin-bottom: 22px; }
  .card--front .brand__name { font-size: 40px; }

  .contact-panel { position: absolute; inset: 0; }

  .contact {
    position: absolute;
    right: 48px;
    top: 112px;
    text-align: right;
    color: var(--ink-light);
  }
  .contact__name {
    font-family: "Cinzel", "Times New Roman", serif;
    font-weight: 600;
    font-size: 30px;
    letter-spacing: 0.03em;
  }
  .contact__title {
    font-family: "Cinzel", "Times New Roman", serif;
    font-size: 20px;
    letter-spacing: 0.12em;
    margin-top: 2px;
  }
  .contact__list { list-style: none; margin-top: 48px; }
  .contact__item {
    display: flex;
    justify-content: flex-end;
    align-items: center;
    gap: 8px;
    font-size: 17px;
    line-height: 1.75;
  }
  .contact__icon { width: 16px; height: 16px; flex: none; }
</style>
</head>
<body>

  <section class="card card--back" aria-label="Card back">
    <div class="brand">
      <div class="brand__mark" aria-hidden="true"></div>
      <div class="brand__name">HARBORLINE<br>RENEWAL</div>
      <p class="tagline">Specializing in Water Damage Restoration</p>
    </div>
  </section>

  <section class="card card--front" aria-label="Card front">
    <div class="brand">
      <div class="brand__mark" aria-hidden="true"></div>
      <div class="brand__name">HARBORLINE<br>RENEWAL</div>
    </div>

    <svg class="contact-panel" viewBox="0 0 880 503" width="880" height="503" aria-hidden="true">
      <circle cx="872" cy="250" r="372" fill="var(--crescent-blue)"/>
      <circle cx="888" cy="248" r="368" fill="#111113"/>
      <circle cx="900" cy="246" r="366" fill="var(--panel-blue)"/>
      <circle cx="760" cy="250" r="150" fill="#ffffff" opacity="0.06"/>
    </svg>

    <div class="contact">
      <div class="contact__name">Darnell Quisby</div>
      <div class="contact__title">Title</div>
      <ul class="contact__list">
        <li class="contact__item">
          <svg class="contact__icon" viewBox="0 0 16 16" aria-hidden="true"><circle cx="8" cy="8" r="7" fill="none" stroke="#fff" stroke-width="1.4"/><path d="M5.5 4.5l1.5 0 .8 2-1 .8a5 5 0 0 0 2 2l.8-1 2 .8v1.5c-3.5.5-7-3-6.1-6.1z" fill="#fff"/></svg>
          <span>555-318-2046</span>
        </li>
        <li class="contact__item">
          <span>Darnell@HarborlineRenewal.example</span>
        </li>
        <li class="contact__item">
          <svg class="contact__icon" viewBox="0 0 16 16" aria-hidden="true"><rect x="2" y="4" width="12" height="9" rx="1" fill="none" stroke="#fff" stroke-width="1.4"/><path d="M2.5 4.5L8 9l5.5-4.5" fill="none" stroke="#fff" stroke-width="1.4"/></svg>
          <span>Darnell@HarborlineRenewal.example</span>
        </li>
        <li class="contact__item">
          <svg class="contact__icon" viewBox="0 0 16 16" aria-hidden="true"><circle cx="8" cy="8" r="6.5" fill="none" stroke="#fff" stroke-width="1.3"/><ellipse cx="8" cy="8" rx="3" ry="6.5" fill="none" stroke="#fff" stroke-width="1.1"/><path d="M1.5 8h13" stroke="#fff" stroke-width="1.1"/></svg>
          <span>www.HarborlineRenewal.example</span>
        </li>
      </ul>
    </div>
  </section>

</body>
</html>
```